Multi-Line Insurance PPC Landing Page - Conversion optimized.

We have a PPC landing page used for the general population to get an insurance quote through an agent's site.

We'd like to improve the page for PPC traffic, make it more conversion friendly.

Site should be a single long page.

We will dynamically change the form and headlines on the page depending on what insurance "line" is being called. ie, Lift, Auto, Home, Business.

The enclosed AI file has all of the raw elements we need. We're looking to enhance the design and conversion ability.

Target Market(s)

General public needed insurance services.

Industry/Entity Type

Insurance Broker

Number of Pages Required

1 page

Font styles to use
Sans Serif

Requirements
Must have
• Form, agent picture, name, address.

```html
<!DOCTYPE html>
<html lang="en">
<head>
<meta charset="utf-8">
<title>Insurance Agent – Get an Instant Insurance Quote</title>
<link href="https://fonts.googleapis.com/css2?family=Open+Sans:wght@400;600;700&display=swap" rel="stylesheet">
<style>
:root{
  --blue:#1f5aa8;
  --blue-dark:#173f78;
  --blue-light:#2f74c8;
  --green:#2f7d1f;
  --green-dark:#23620f;
  --ink:#333;
  --muted:#666;
  --line:#d6d6d6;
  --panel:#f0f0f0;
  --band:#e6e6e6;
  --white:#fff;
}
*{box-sizing:border-box;margin:0;padding:0}
html,body{width:1200px;height:2184px;overflow:hidden}
body{font-family:"Open Sans",Arial,sans-serif;color:var(--ink);background:var(--white);position:relative}

/* header */
.site-header{position:absolute;left:0;top:0;width:1200px;height:92px;background:var(--white);border-bottom:1px solid var(--line)}
.brand{position:absolute;left:40px;top:24px;font-size:36px;font-weight:700;color:var(--blue);letter-spacing:-.5px}
.brand-dot{display:inline-block;width:12px;height:12px;background:var(--blue);margin-left:6px;vertical-align:middle}
.header-phone{position:absolute;right:40px;top:16px;display:flex;align-items:center;gap:14px}
.header-phone svg{width:44px;height:44px}
.header-phone small{display:block;font-size:14px;color:var(--muted)}
.header-phone strong{display:block;font-size:26px;color:var(--blue);font-weight:700;line-height:1.1}

/* hero */
.hero{position:absolute;left:0;top:92px;width:1200px;height:520px;background:linear-gradient(120deg,#7d8fa6 0%,#4d6583 35%,#2c3e55 70%,#1e2c3f 100%)}
.hero-label{position:absolute;left:100px;top:240px;width:380px;height:92px;background:rgba(30,30,30,.75);color:var(--white);font-size:38px;font-weight:400;line-height:92px;padding-left:28px;border-left:6px solid var(--white);letter-spacing:.5px}
.hero-arrow{position:absolute;top:318px;width:30px;height:56px;background:rgba(40,40,40,.8)}
.hero-arrow svg{width:30px;height:56px}
.hero-arrow.prev{left:0}
.hero-arrow.next{right:0}

/* lines */
.lines{position:absolute;left:120px;top:540px;width:960px;display:flex;gap:24px}
.line-card{flex:1;height:270px;background:var(--white);box-shadow:0 6px 16px rgba(0,0,0,.25);text-align:center;padding-top:26px}
.line-icon{width:92px;height:92px;border-radius:50%;background:var(--blue);margin:0 auto;display:flex;align-items:center;justify-content:center}
.line-icon svg{width:52px;height:52px}
.line-card h3{font-size:26px;font-weight:700;margin-top:10px;color:var(--ink)}
.line-card p{font-size:13px;line-height:17px;color:var(--muted);padding:4px 22px 0}
.btn-quote{display:inline-block;margin-top:12px;background:var(--green);color:var(--white);font-size:13px;font-weight:700;padding:6px 18px;letter-spacing:.5px}

/* quote section */
.quote-section{position:absolute;left:120px;top:872px;width:960px;height:400px;display:flex;gap:20px}
.agent-card{width:300px;height:400px;background:var(--panel);text-align:center;padding-top:26px}
.agent-photo{width:160px;height:160px;border-radius:50%;margin:0 auto;border:6px solid var(--blue);background:radial-gradient(circle at 50% 40%,#d9c3ad 0%,#8f7a68 45%,#34475e 100%)}
.agent-name{font-size:28px;font-weight:600;margin-top:20px}
.agent-phone{font-size:20px;font-weight:700;color:var(--blue);margin-top:8px;display:flex;justify-content:center;align-items:center;gap:8px}
.agent-phone svg{width:24px;height:24px}
.agent-address{font-size:15px;color:var(--muted);margin-top:20px;line-height:22px}

.quote-form{flex:1;background:var(--panel);padding:22px 30px}
.quote-form h2{font-size:27px;font-weight:400;color:var(--blue);border-bottom:1px solid var(--line);padding-bottom:10px}
.quote-form h2 b{font-weight:700}
.quote-form h2 span{color:var(--ink)}
.form-grid{display:grid;grid-template-columns:1fr 1fr;column-gap:30px;row-gap:8px;margin-top:14px}
.field label{display:block;font-size:13px;color:var(--ink);margin-bottom:3px}
.input{height:30px;background:var(--white);border:1px solid var(--line);font-size:13px;color:#999;line-height:28px;padding-left:8px}
.split{display:flex;gap:6px}
.split .input{flex:1}
.btn-submit{display:inline-block;margin-top:14px;background:var(--green-dark);color:var(--white);font-size:15px;font-weight:700;padding:8px 30px;letter-spacing:.5px}

/* about */
.about{position:absolute;left:120px;top:1290px;width:960px;text-align:center}
.about h2{font-size:33px;font-weight:700;color:var(--blue)}
.about h2 span{font-weight:400}
.about p{font-size:14px;line-height:21px;color:var(--muted);margin-top:10px}

/* reviews */
.reviews{position:absolute;left:0;top:1452px;width:1200px;height:372px;background:var(--band)}
.reviews-title{position:absolute;left:0;top:20px;width:1200px;display:flex;justify-content:center;align-items:center;gap:24px}
.reviews-title h2{font-size:32px;font-weight:700;color:var(--blue);background:var(--white);padding:4px 28px}
.reviews-title h2 span{color:var(--ink)}
.title-arrow svg{width:22px;height:32px}
.review-list{position:absolute;left:120px;top:100px;width:960px;display:flex;gap:40px}
.review-card{flex:1}
.review-body{background:var(--white);padding:22px 26px 22px 66px;position:relative;font-size:13px;line-height:19px;color:var(--muted);height:170px}
.review-body .quote-mark{position:absolute;left:18px;top:8px;font-size:64px;line-height:64px;color:#bbb;font-family:Georgia,serif}
.reviewer{display:flex;align-items:center;gap:14px;margin-top:10px;padding-left:24px}
.reviewer-photo{width:70px;height:70px;border-radius:50%;border:4px solid var(--white);background:radial-gradient(circle at 50% 40%,#c9ab92 0%,#7b6555 55%,#3a3a3a 100%)}
.reviewer-name{font-size:14px;color:var(--green);font-weight:600}

/* companies */
.companies{position:absolute;left:0;top:1840px;width:1200px;height:180px}
.companies h2{position:absolute;left:440px;top:0;width:320px;height:56px;border:2px solid var(--blue);text-align:center;font-size:28px;font-weight:700;color:var(--blue);line-height:52px}
.companies h2 span{color:var(--ink)}
.company-row{position:absolute;left:90px;top:84px;width:1020px;display:flex;align-items:center;justify-content:space-between}
.company-row .nav svg{width:22px;height:32px}
.company{display:flex;align-items:center;gap:8px;font-size:26px;font-weight:700;color:#444}
.company i{display:block;width:22px;height:22px;background:#444}
.company i.round{border-radius:50%}

/* footer */
.site-footer{position:absolute;left:0;top:2018px;width:1200px;height:166px;background:var(--blue)}
.disclaimer{position:absolute;left:120px;top:14px;width:960px;text-align:center;color:var(--white)}
.disclaimer h4{font-size:15px;font-weight:700}
.disclaimer p{font-size:11px;line-height:16px;margin-top:4px;opacity:.9}
.footer-bottom{position:absolute;left:0;top:116px;width:1200px;height:50px;background:var(--blue-dark);color:var(--white)}
.footer-bottom small{position:absolute;left:40px;top:16px;font-size:13px}
.footer-bottom .footer-brand{position:absolute;right:40px;top:6px;font-size:28px;font-weight:600}
</style>
</head>
<body>

<header class="site-header">
  <div class="brand">Insurance Agent<span class="brand-dot"></span></div>
  <div class="header-phone">
    <svg viewBox="0 0 44 44"><circle cx="22" cy="22" r="21" fill="none" stroke="#1f5aa8" stroke-width="2"/><path d="M15 12c2-1 3 0 4 3l1 3c0 1-1 2-2 3 1 3 3 5 6 6 1-1 2-2 3-2l3 1c3 1 4 2 3 4-1 3-3 4-6 3-7-2-12-7-14-14-1-3 0-6 2-7z" fill="#1f5aa8"/></svg>
    <div><small>Get a quick quote by phone</small><strong>(555) 014-2200</strong></div>
  </div>
</header>

<section class="hero">
  <div role="img" aria-label="Businessman holding protective hands over a small white car" style="position:absolute;inset:0"></div>
  <div class="hero-arrow prev"><svg viewBox="0 0 30 56"><path d="M19 18l-9 10 9 10" fill="none" stroke="#fff" stroke-width="3"/></svg></div>
  <h1 class="hero-label">AUTO INSURANCE</h1>
  <div class="hero-arrow next"><svg viewBox="0 0 30 56"><path d="M11 18l9 10-9 10" fill="none" stroke="#fff" stroke-width="3"/></svg></div>
</section>

<section class="lines">
  <article class="line-card">
    <div class="line-icon"><svg viewBox="0 0 52 52"><rect x="8" y="20" width="18" height="16" fill="#fff"/><rect x="12" y="12" width="10" height="10" fill="none" stroke="#fff" stroke-width="3"/><rect x="30" y="8" width="3" height="30" fill="#fff"/><rect x="33" y="34" width="12" height="3" fill="#fff"/><circle cx="12" cy="40" r="4" fill="#fff"/><circle cx="24" cy="40" r="4" fill="#fff"/></svg></div>
    <h3>Lift</h3>
    <p>Lorem ipsum dolor sit amet, consectetuer adipiscing elit, sed diam nonummy nibh euismod</p>
    <span class="btn-quote">GET A QUOTE</span>
  </article>
  <article class="line-card">
    <div class="line-icon"><svg viewBox="0 0 52 52"><path d="M10 26l5-11h22l5 11v12H10z" fill="#fff"/><rect x="17" y="18" width="18" height="7" fill="#1f5aa8"/><circle cx="16" cy="31" r="3" fill="#1f5aa8"/><circle cx="36" cy="31" r="3" fill="#1f5aa8"/><rect x="11" y="37" width="6" height="6" fill="#fff"/><rect x="35" y="37" width="6" height="6" fill="#fff"/></svg></div>
    <h3>Auto</h3>
    <p>Lorem ipsum dolor sit amet, consectetuer adipiscing elit, sed diam nonummy nibh euismod</p>
    <span class="btn-quote">GET A QUOTE</span>
  </article>
  <article class="line-card">
    <div class="line-icon"><svg viewBox="0 0 52 52"><path d="M26 8L6 26h6v18h10V33h8v11h10V26h6z" fill="#fff"/></svg></div>
    <h3>Home</h3>
    <p>Lorem ipsum dolor sit amet, consectetuer adipiscing elit, sed diam nonummy nibh euismod</p>
    <span class="btn-quote">GET A QUOTE</span>
  </article>
  <article class="line-card">
    <div class="line-icon"><svg viewBox="0 0 52 52"><rect x="6" y="16" width="40" height="26" rx="3" fill="#fff"/><rect x="19" y="10" width="14" height="8" rx="2" fill="none" stroke="#fff" stroke-width="3"/><rect x="6" y="27" width="40" height="2" fill="#1f5aa8"/></svg></div>
    <h3>Business</h3>
    <p>Lorem ipsum dolor sit amet, consectetuer adipiscing elit, sed diam nonummy nibh euismod</p>
    <span class="btn-quote">GET A QUOTE</span>
  </article>
</section>

<section class="quote-section">
  <aside class="agent-card">
    <div class="agent-photo" role="img" aria-label="Portrait photo of the insurance agent"></div>
    <div class="agent-name">Marcus Hale - Agent</div>
    <div class="agent-phone"><svg viewBox="0 0 24 24"><circle cx="12" cy="12" r="12" fill="#1f5aa8"/><path d="M8 6c1 0 2 0 2 2l1 2c0 1-1 1-1 2 1 1 2 2 3 2 0-1 1-1 2-1l2 1c1 0 1 1 1 2-1 2-2 2-4 2-4-1-7-4-8-8 0-2 1-3 2-4z" fill="#fff"/></svg>(555) 014-2270</div>
    <div class="agent-address">418 Orchard Lane<br>Brookfield, CA 90555</div>
  </aside>
  <form class="quote-form">
    <h2><b>Get An Instant</b> <span>Insurance Quote.</span></h2>
    <div class="form-grid">
      <div class="field"><label>First Name:</label><div class="input"></div></div>
      <div class="field"><label>Height/Weight:</label><div class="input"></div></div>
      <div class="field"><label>Sex:</label><div class="input">Select</div></div>
      <div class="field"><label>Tobacco Use:</label><div class="input">Select</div></div>
      <div class="field"><label>Date of Birth:</label><div class="split"><div class="input">Month</div><div class="input">Day</div><div class="input">Year</div></div></div>
      <div class="field"><label>Phone:</label><div class="input"></div></div>
      <div class="field"><label>Current Health:</label><div class="input">Select</div></div>
      <div class="field"><label>Email:</label><div class="input"></div></div>
    </div>
    <span class="btn-submit">SUBMIT</span>
  </form>
</section>

<section class="about">
  <h2>About <span>Insurance Agent</span></h2>
  <p>Lorem ipsum dolor sit amet, consectetuer adipiscing elit, sed diam nonummy nibh euismod tincidunt ut laoreet dolore magna aliquam erat volutpat. Ut wisi enim ad minim veniam, quis nostrud exerci tation ullamcorper suscipit lobortis nisl ut aliquip ex ea commodo consequat. Duis autem vel eum iriure dolor in hendrerit in vulputate velit esse molestie consequat, vel illum dolore eu feugiat nulla facilisis at vero eros et accumsan et iusto odio dignissim qui blandit praesent.</p>
</section>

<section class="reviews">
  <div class="reviews-title">
    <span class="title-arrow"><svg viewBox="0 0 22 32"><path d="M15 6L5 16l10 10" fill="none" stroke="#333" stroke-width="4"/></svg></span>
    <h2>Our Customer <span>Review</span></h2>
    <span class="title-arrow"><svg viewBox="0 0 22 32"><path d="M7 6l10 10-10 10" fill="none" stroke="#333" stroke-width="4"/></svg></span>
  </div>
  <div class="review-list">
    <article class="review-card">
      <div class="review-body"><span class="quote-mark">“</span>Lorem ipsum dolor sit amet consectetuer sed diam nibh euismod tincidunt ut laoreet dolore magna aliquam erat volutpat. Ut wisi enim ad minim veniam quis nostrud exerci tation ullamcorper suscipit lobortis nisl ut aliquip ex ea commodo consequat.</div>
      <div class="reviewer"><div class="reviewer-photo" role="img" aria-label="Customer photo"></div><span class="reviewer-name">Mr Owen Hartley</span></div>
    </article>
    <article class="review-card">
      <div class="review-body"><span class="quote-mark">“</span>Lorem ipsum dolor sit amet consectetuer sed diam nibh euismod tincidunt ut laoreet dolore magna aliquam erat volutpat. Ut wisi enim ad minim veniam quis nostrud exerci tation ullamcorper suscipit lobortis nisl ut aliquip ex ea commodo consequat.</div>
      <div class="reviewer"><div class="reviewer-photo" role="img" aria-label="Customer photo"></div><span class="reviewer-name">Mr Owen Hartley</span></div>
    </article>
  </div>
</section>

<section class="companies">
  <h2>Insurance <span>Company</span></h2>
  <div class="company-row">
    <span class="nav"><svg viewBox="0 0 22 32"><path d="M15 6L5 16l10 10" fill="none" stroke="#1f5aa8" stroke-width="4"/></svg></span>
    <span class="company"><i></i>Ledgerly</span>
    <span class="company"><i class="round"></i>Meadowline</span>
    <span class="company"><i></i>Stonebay</span>
    <span class="company">Vantro</span>
    <span class="company">Northwave<i class="round"></i></span>
    <span class="nav"><svg viewBox="0 0 22 32"><path d="M7 6l10 10-10 10" fill="none" stroke="#1f5aa8" stroke-width="4"/></svg></span>
  </div>
</section>

<footer class="site-footer">
  <div class="disclaimer">
    <h4>Disclaimer</h4>
    <p>Lorem ipsum dolor sit amet, consectetuer adipiscing elit, sed diam nonummy nibh euismod tincidunt ut laoreet dolore magna aliquam erat volutpat. Ut wisi enim ad minim veniam, quis nostrud exerci tation ullamcorper suscipit lobortis nisl ut aliquip ex ea commodo consequat. Duis autem vel eum iriure dolor in hendrerit in vulputate velit esse molestie consequat vel illum dolore.</p>
  </div>
  <div class="footer-bottom">
    <small>© 2015 Insurance Agent. All Rights Reserved.</small>
    <span class="footer-brand">Insurance Agent</span>
  </div>
</footer>

</body>
</html>
```